Business card for law firm

Need business card for new law firm. Think confident, authoritative, conservative, but not stuffy or old-fashioned.

Contact Information for Business Card

Content for card - logo (uploaded), plus the following:

Paul Whitcombe (larger font)
Managing Partner (larger font, but not as large as name)
Level 9, 7 Ferris Lane
Sydney NSW 2000
Main Tel 02 9364 2710
Direct Tel 02 8472 3159
Email paul@qvlegal.com.au
www.qvlegal.com.au

Letterhead design should include logo plus:
Level 9, 7 Ferris Lane
Sydney NSW 2000
Tel 02 8472 3159
www.qvlegal.com.au

```html
<!DOCTYPE html>
<html lang="en">
<head>
<meta charset="utf-8">
<title>Quayvale Legal — Business Card</title>
<link href="https://fonts.googleapis.com/css2?family=Cinzel:wght@400&family=Open+Sans:wght@400&display=swap" rel="stylesheet">
<style>
  :root {
    --stage: #5b5b5b;
    --navy: #0c1d5a;
    --white: #ffffff;
    --ink: #111111;
  }
  * { margin: 0; padding: 0; box-sizing: border-box; }
  html, body {
    width: 1200px;
    height: 802px;
    overflow: hidden;
    background: var(--stage);
  }
  .canvas {
    position: relative;
    width: 1200px;
    height: 802px;
  }
  .card {
    position: absolute;
    top: 274px;
    width: 442px;
    height: 264px;
  }
  .card--front {
    left: 136px;
    background: var(--navy);
    color: var(--white);
  }
  .card--back {
    left: 624px;
    background: var(--white);
    color: var(--ink);
  }

  /* Front */
  .front-brand {
    position: absolute;
    right: 24px;
    top: 50px;
    font-family: "Cinzel", serif;
    font-size: 23px;
    letter-spacing: 0.5px;
    line-height: 1;
    white-space: nowrap;
  }
  .person {
    position: absolute;
    right: 24px;
    top: 120px;
    text-align: right;
  }
  .person__name {
    font-family: "Cinzel", serif;
    font-size: 18px;
    line-height: 20px;
    letter-spacing: 0.2px;
  }
  .person__role {
    font-family: "Open Sans", sans-serif;
    font-size: 13px;
    line-height: 16px;
  }
  .contacts {
    position: absolute;
    right: 24px;
    top: 163px;
    list-style: none;
    font-family: "Open Sans", sans-serif;
    font-size: 12.5px;
    line-height: 16px;
    text-align: right;
  }
  .contacts li {
    display: flex;
    justify-content: flex-end;
    align-items: center;
    gap: 3px;
  }
  .contacts .tag { font-size: 10.5px; }
  .contacts svg { width: 10px; height: 10px; flex: none; }
  .address {
    position: absolute;
    right: 24px;
    top: 229px;
    font-family: "Open Sans", sans-serif;
    font-size: 12.5px;
    line-height: 16px;
    white-space: nowrap;
  }

  /* Back */
  .back-mark {
    position: absolute;
    left: 197px;
    top: 78px;
    width: 48px;
    height: 48px;
    background: var(--navy);
  }
  .back-brand {
    position: absolute;
    left: 0;
    right: 0;
    top: 150px;
    text-align: center;
    font-family: "Cinzel", serif;
    font-size: 32px;
    line-height: 1;
    letter-spacing: 0.5px;
    white-space: nowrap;
  }
</style>
</head>
<body>
<main class="canvas">

  <section class="card card--front" aria-label="Card front">
    <p class="front-brand">QUAYVALE LEGAL</p>

    <div class="person">
      <p class="person__name">PAUL WHITCOMBE</p>
      <p class="person__role">Managing Partner</p>
    </div>

    <ul class="contacts">
      <li>02 9364 2710
        <svg viewBox="0 0 10 10" aria-hidden="true"><path fill="#fff" d="M1 3.2C1 2 2.5 1.4 5 1.4S9 2 9 3.2V4H7V3.2H3V4H1z M2.4 5h5.2L9 8.6H1z"/></svg>
      </li>
      <li>02 8472 3159 <span class="tag">(DIRECT)</span>
        <svg viewBox="0 0 10 10" aria-hidden="true"><path fill="#fff" d="M1 3.2C1 2 2.5 1.4 5 1.4S9 2 9 3.2V4H7V3.2H3V4H1z M2.4 5h5.2L9 8.6H1z"/></svg>
      </li>
      <li>paul@qvlegal.com.au
        <svg viewBox="0 0 10 10" aria-hidden="true"><rect x="0.5" y="2" width="9" height="6.5" fill="#fff"/><path d="M0.8 2.3L5 5.6 9.2 2.3" fill="none" stroke="#0c1d5a" stroke-width="0.9"/></svg>
      </li>
      <li>www.qvlegal.com.au
        <svg viewBox="0 0 10 10" aria-hidden="true"><circle cx="5" cy="5" r="4.5" fill="#fff"/><path d="M5 0.5C3 2.5 3 7.5 5 9.5M5 0.5C7 2.5 7 7.5 5 9.5M0.7 5H9.3" fill="none" stroke="#0c1d5a" stroke-width="0.8"/></svg>
      </li>
    </ul>

    <p class="address">Level 9, 7 Ferris Lane&nbsp; Sydney NSW 2000</p>
  </section>

  <section class="card card--back" aria-label="Card back">
    <div class="back-mark" aria-hidden="true"></div>
    <p class="back-brand">QUAYVALE LEGAL</p>
  </section>

</main>
</body>
</html>
```